High Tech Real Estate Startup needs a business card

We are developing an innovative real estate marketing product based around advanced search and virtual reality.

We talk to people, we need business cards.

Target Market(s)

The target market is technology professionals and realtors.

Contact Information for Business Card

The information to be included will include

Name
Title
Phone Number
E-mail Address
www.zelquin.com

It should use simple iconography for each one of those fields.

Font styles to use
Other font styles liked:
• Co, Jubilat, Avenir

Colors

Designer to choose colors to be used in the design.

Requirements
Must have
• Clean aesthetic,
• Good use of negative space.
• It should use our company logo, shown in the attached file. It is able to use the negative of that logo (coloured font and white background) and I have attached other acceptable accent colours in a swatch file.
Should not have
• Should not be too busy
• No extraneous text (slogans, tag lines etc)

```html
<!DOCTYPE html>
<html lang="en">
<head>
<meta charset="utf-8">
<title>Zelquin Business Card</title>
<link rel="stylesheet" href="https://fonts.googleapis.com/css2?family=Open+Sans:wght@400;600;700&display=swap">
<style>
  :root {
    --page-bg: #2b2d30;
    --card-bg: #1c2124;
    --accent: #1fb3bb;
    --logo-silver: #c9cdd0;
  }
  * { box-sizing: border-box; margin: 0; padding: 0; }
  html, body {
    width: 1200px; height: 800px; overflow: hidden;
    background: var(--page-bg);
    font-family: "Open Sans", Arial, sans-serif;
  }
  .stage {
    width: 1200px; height: 800px;
    display: flex; align-items: center; justify-content: center; gap: 40px;
  }
  .card {
    width: 540px; height: 309px;
    background: var(--card-bg);
    border-radius: 3px;
    position: relative;
  }
  .card-front { display: flex; align-items: center; justify-content: center; }
  .brand-name {
    font-weight: 600; font-size: 50px; letter-spacing: 4px;
    color: var(--logo-silver);
  }
  .card-back {
    display: flex; align-items: center; justify-content: center; gap: 22px;
    color: var(--accent);
  }
  .person { text-align: right; }
  .person-name { font-weight: 700; font-size: 21px; letter-spacing: 0.5px; line-height: 1.1; }
  .person-title { font-weight: 400; font-size: 14px; line-height: 1.2; }
  .divider { width: 1px; height: 62px; background: var(--accent); }
  .contacts { list-style: none; display: flex; flex-direction: column; gap: 4px; }
  .contact { display: flex; align-items: center; gap: 8px; font-size: 13px; line-height: 1.3; }
  .contact svg { width: 12px; height: 12px; fill: var(--accent); flex: none; }
</style>
</head>
<body>
<main class="stage">
  <section class="card card-front" aria-label="Card front">
    <span class="brand-name">ZELQUIN</span>
  </section>
  <section class="card card-back" aria-label="Card back">
    <div class="person">
      <p class="person-name">DARA KELLS</p>
      <p class="person-title">Manager</p>
    </div>
    <span class="divider"></span>
    <ul class="contacts">
      <li class="contact">
        <svg viewBox="0 0 12 12" aria-hidden="true"><path d="M1 4c0-2 1-3 2-3h6c1 0 2 1 2 3H8.5V3h-5v1zM2 5h8l1 6H1z"/></svg>
        555-210-4418
      </li>
      <li class="contact">
        <svg viewBox="0 0 12 12" aria-hidden="true"><path d="M0 2h12v8H0z M1 3l5 4 5-4" stroke="#1c2124" stroke-width="1"/></svg>
        info@zelquin.com
      </li>
      <li class="contact">
        <svg viewBox="0 0 12 12" aria-hidden="true"><circle cx="6" cy="6" r="5.5"/><path d="M0.5 6h11M6 0.5c-3 3-3 8 0 11M6 0.5c3 3 3 8 0 11" stroke="#1c2124" stroke-width="0.8" fill="none"/></svg>
        www.zelquin.com
      </li>
    </ul>
  </section>
</main>
</body>
</html>
```